TalkSift Website Re-skin

TalkSift.com needs to be re-skinned. The form design of the website and talksift logo are is to stay as-is. The images, type font and background color need to be updated to attempt to achieve a professionally-progressive first impression. We are also amiable to any recommended copy changes, but the main focus of this initiative is to replace the tired and muted existing images, background, and type font. I have included a number of websites that have the look and feel that we would like to inspire the refresh.... These websites also do a good job to include images that blend a computer, ipad, or iphone with a somewhat blurred background.

I included two company overview documents to describe the service. You can also log into the site and receive 5 Free interviews so that you can experience the site yourself in about 10 minutes.

Another high level overview is described in this video link:
http://clipmarsh.example/q7Lr2-Xpdwe
Updates

We received some questions from a few designers and I want to make sure that I share my responses with everyone.  

How many pages do we want:  
We would like 3 pages.  The Home Page, the Login Page, and the Create Account Page.  Note: The large majority of the work should be focused on the Home Page.  The Login and Create Account pages just need to have the background and overall theme from the Home Page design.  

Is coding a must for the Project:  
Coding is highly preferred as it will help reduce the process of splicing up the artwork files.  As such, our preference is to obtain the coding with the project. 

What type of Coding do we want?
HTML/CSS is acceptable

Note:  I also added some Logo .png files onto the craft yard site

Target Market(s)

Please refer to the attached "company description" and "business overview" documents. General target audience is small, medium and large organizations seeking to reduce the time and cost to interview qualified job candidates. Given that TalkSift serves small to large organizations, we would like our design to error on the size of "professionally progressive" such that it has the visual appearance of being sophisticated and technologically sound.

Industry/Entity Type

Computer

Requirements
Must have
• Seeking to have 3 pages re-skinned. The Home Page, the Login Page, and the Create Account Page. Note. The Login and Create Account Pages should be very straight forward with limited work required as we seek little design change for them and would like them to carry over the theme and colors from the Home Page. Hence, re-skinning the home page with the elements described below is the major focus.

Top of Home Page: Replace main image of lady coming out of resume/ipad screen with an image very similar to the one on the attached file titled "plinko home page lady" Note: Plinko changed its name to Brisel so duplicating this approach is okay to mimic this image without issue. We especially like this image as it is colorful and visually describes the service we provide.

The layout of the "Oru iPad" and "Telvo Home page i-pad" files that are attached are nice. There may be a way to leverage the plinko lady with the Oru Ipad image to make a nice visual.

Verbiage: Change copy from "Welcome to Talksift! Talksift is your fully automated interviewing solution. Personalized to your brand, you will save time and money selecting the best candidates" To Now Read: "Humanize and accelerate your interview screening process with TalkSift."

Background: We really like the way that Oru changes their back-grounds as the themes/subjects change when scrolling down their main web page. Achieving this sort of experience would be ideal. It is also acceptable to have a more contrasting background color that may be darker. If this is done, then the words could be in white. This is not a requirement, just some general direction.

Font type: We like the font type from Oru (see attached file titled "Oru iPad")

Font Color: Okay to change font from the dull blue that we have today and use a different more contrasting or popping color.

We like outlining steps 1 through 4 but prefer to replace the people holding the placards with some other images that are potentially in a family of images that all tie together.

It is okay to keep the images in the "Responsive Layout" section of the site (located about 3/4ths of the way down the page) as these seem to be more current and do a good job to illustrate images with an ipad or computer.

Benefits Section: Prefer to change this section. Listing nine (9) separate benefits are too many to make any impact. Advocate illustrating the following benefits:
- "Reduce time and cost to screen candidates"
- "Design site with your logo and colors"
- "Customize interview questions for all your postings"
- "Interview candidates anywhere in the world"
- "Review candidate video's anytime / anywhere"

Nice to have
• Potential to add an image whereby it shows / illustrates talksift's administrative portal "talksift admin portal" (attached) to an image of an ipad screen similar to how the attached images for the following websites: "Telvo" "WeareHalcyon" and "marshbell"

```html
<!DOCTYPE html>
<html lang="en">
<head>
<meta charset="utf-8">
<title>TalkSift</title>
<link href="https://fonts.googleapis.com/css2?family=Arimo:wght@400;700&display=swap" rel="stylesheet">
<style>
:root{
  --brand:#216d9a;
  --brand-dark:#1b5d86;
  --ink:#333;
  --muted:#8a8a8a;
  --band:#efefef;
  --band-2:#e6e6e6;
  --footer:#595959;
  --line:#cfcfcf;
}
*{box-sizing:border-box;margin:0;padding:0}
html,body{width:745px;height:1200px;overflow:hidden}
body{font-family:Arimo,Arial,sans-serif;color:var(--ink);background:#fff;position:relative}
.abs{position:absolute}
.btn{background:var(--brand-dark);color:#fff;display:flex;align-items:center;justify-content:center}

.header{left:0;top:0;width:745px;height:66px;background:var(--brand);border-bottom:1px solid #5b9cc4}
.logo{left:82px;top:13px;display:flex;align-items:center;gap:5px;color:#fff}
.logo-mark{width:38px;height:38px;border-radius:50%;background:#fff}
.logo-name{font-size:14px;font-weight:700;letter-spacing:1px;line-height:1}
.logo-tag{font-size:6.5px;letter-spacing:.8px;margin-top:3px}
.login{left:595px;top:6px;width:68px;height:22px;border-radius:4px;background:#e6e6e6;border:1px solid #cfcfcf;color:#444;font-size:11px;display:flex;align-items:center;justify-content:center;gap:6px}
.login i{width:14px;height:11px;background:#7a7a7a;border-radius:40%}
.nav{right:82px;top:44px;display:flex;gap:23px;font-size:7.5px;color:#fff}
.nav .on{color:#6fc1ee}

.hero{left:0;top:67px;width:745px;height:248px;background:linear-gradient(90deg,#d9cdc8 0%,#e2e8ec 18%,#e9f1f5 45%,#d8e8ef 75%,#e4eef2 100%)}
.hero-photo{left:372px;top:112px;width:290px;height:203px;border-radius:14px 14px 0 0;background:linear-gradient(160deg,#2c2f33 0%,#c9ab93 30%,#8f9fb0 55%,#dcbca2 85%,#c89c7f 100%)}
.hero-h1{left:113px;top:138px;font-size:29px;color:var(--brand)}
.hero-h2{left:113px;top:176px;font-size:19px;color:var(--brand)}
.learn{left:116px;top:221px;width:77px;height:25px;font-size:7.5px}
.arrow{width:14px;height:14px;border:1px solid #9fb0ba;border-radius:50%;top:181px}

.steps{left:0;top:315px;width:740px;height:160px;background:var(--band)}
.steps-title{left:0;top:330px;width:745px;text-align:center;font-size:16px;color:var(--brand)}
.steps-sub{left:0;top:363px;width:745px;text-align:center;font-size:7.5px;color:#555}
.step{top:393px;display:flex;gap:9px;width:140px}
.step-icon{width:46px;height:46px;border-radius:50%;background:var(--brand);flex:none;display:flex;align-items:center;justify-content:center}
.step-title{font-size:10px;color:var(--brand);line-height:12px;margin-top:6px}
.step-text{font-size:6.5px;color:#999;line-height:12px;width:75px}

.devices{left:82px;top:502px;width:305px;height:148px;border-radius:6px;background:linear-gradient(180deg,#f2f4f5 0%,#dfe7ec 45%,#c7d2d9 100%)}
.value-h{left:449px;top:510px;font-size:21px;color:var(--brand);font-weight:400}
.value-p{left:449px;top:546px;width:200px;font-size:7px;line-height:15.7px;color:var(--muted)}
.value-p span{color:var(--brand)}

.pricing-h{left:82px;top:698px;font-size:16px;color:var(--brand);font-weight:400}
.price{left:86px;top:729px;width:339px;border-collapse:collapse;font-size:9px}
.price td{border:1px solid var(--line);background:#f3f3f3;text-align:center;color:#444;width:68px}
.price td:first-child{text-align:left;padding-left:7px;font-size:10px;color:#222}
.price tr:nth-child(1) td,.price tr:nth-child(3) td,.price tr:nth-child(4) td{height:42px}
.price tr:nth-child(2) td{height:45px}
.try{display:inline-flex;height:22px;padding:0 5px;font-size:9px}

.benefits{left:458px;top:690px;width:205px;height:203px;border:1px solid var(--line)}
.benefits-h{height:33px;background:var(--brand);color:#fff;font-size:16px;padding:7px 6px}
.benefit{height:23.3px;border-bottom:1px solid #e1e1e1;display:flex;align-items:center;gap:10px;padding-left:9px;font-size:6.5px;color:#777}
.benefit i{width:8px;height:8px;background:#444;border-radius:2px}

.admin{left:0;top:931px;width:745px;height:191px;background:var(--band-2)}
.phone{left:118px;top:933px;width:152px;height:189px;background:linear-gradient(100deg,#e5e5e5 0%,#d9b39a 30%,#f5f5f5 38%,#f5f5f5 72%,#dcb8a0 85%,#e5e5e5 100%)}
.admin-h{left:358px;top:950px;font-size:21px;color:var(--brand);font-weight:400}
.admin-p{left:361px;top:984px;width:285px;font-size:7px;line-height:15.3px;color:var(--muted)}
.read{left:362px;top:1085px;width:83px;height:26px;font-size:10px}

.footer{left:0;top:1130px;width:745px;height:70px;background:var(--footer)}
.social{left:341px;top:1146px;display:flex;gap:3px}
.social i{width:15px;height:15px;border-radius:50%;background:#fff}
.copy{left:0;top:1176px;width:745px;text-align:center;font-size:7px;color:#fff}
</style>
</head>
<body>
<header class="abs header"></header>
<div class="abs logo"><div class="logo-mark"></div><div><div class="logo-name">TALKSIFT</div><div class="logo-tag">BRING RESUMES TO LIFE</div></div></div>
<div class="abs login"><i></i>Login</div>
<nav class="abs nav"><span class="on">Home</span><span>About us</span><span>How it work</span><span>Testimonials</span><span>Blog</span><span>Contact us</span></nav>

<div class="abs hero" role="img" aria-label="Blurred bright office background"></div>
<div class="abs hero-photo" role="img" aria-label="Hands holding a tablet with a candidate reaching out from a resume on screen"></div>
<h1 class="abs hero-h1" style="font-weight:400">Review candidate</h1>
<div class="abs hero-h2">video's anytime / anywhere</div>
<div class="abs btn learn">LEARN MORE</div>
<div class="abs arrow" style="left:49px"></div>
<div class="abs arrow" style="left:684px"></div>

<section class="abs steps"></section>
<div class="abs steps-title">4 simple steps!</div>
<div class="abs steps-sub">Pre-screen your interviews and hire who you need.</div>
<div class="abs step" style="left:82px"><div class="step-icon"><svg width="22" height="22" viewBox="0 0 22 22"><path d="M2 9h8V5l6 6-6 6v-4H2z" fill="#fff"/><path d="M13 3h6v16h-6" stroke="#fff" stroke-width="2" fill="none"/></svg></div><div><div class="step-title">Sign<br>up...</div><div class="step-text">TalkSift video interview-ing makes interviewing a snap...</div></div></div>
<div class="abs step" style="left:234px"><div class="step-icon"><svg width="24" height="24" viewBox="0 0 24 24"><circle cx="10" cy="6" r="4" fill="#fff"/><path d="M2 20c0-6 4-8 8-8s5 1 6 3v5z" fill="#fff"/><circle cx="18" cy="18" r="5" fill="#fff"/><path d="M18 15v6M15 18h6" stroke="#216d9a" stroke-width="1.6"/></svg></div><div><div class="step-title">Create<br>Posting...</div><div class="step-text">TalkSift video interview-ing makes interviewing a snap...</div></div></div>
<div class="abs step" style="left:384px"><div class="step-icon"><svg width="24" height="24" viewBox="0 0 24 24" fill="#fff"><circle cx="12" cy="4" r="2.5"/><rect x="10" y="7" width="4" height="4"/><path d="M4 13h16M4 13v3M12 11v5M20 13v3" stroke="#fff" stroke-width="1.2"/><circle cx="4" cy="18" r="2"/><circle cx="12" cy="18" r="2"/><circle cx="20" cy="18" r="2"/></svg></div><div><div class="step-title">Invite<br>Candidates...</div><div class="step-text">TalkSift video interview-ing makes interviewing a snap...</div></div></div>
<div class="abs step" style="left:534px"><div class="step-icon"><svg width="20" height="22" viewBox="0 0 20 22"><rect x="2" y="1" width="16" height="20" fill="none" stroke="#fff" stroke-width="1.6"/><path d="M5 6h2M9 6h6M5 11h2M9 11h6M5 16h2M9 16h6" stroke="#fff" stroke-width="1.4"/></svg></div><div><div class="step-title">Review<br>Candidates...</div><div class="step-text">TalkSift video interview-ing makes interviewing a snap...</div></div></div>

<div class="abs devices" role="img" aria-label="Tablet, phone, desktop and laptop showing the create account form"></div>
<h2 class="abs value-h">The TalkSift Value</h2>
<p class="abs value-p">TalkSift video interviewing makes prescreening potential employees quick, safe, and extremely easy. With no con-tracts, hidden fees, or complicated user interfaces, we make video screening / interviewing a snap.TalkSift video interviewing makes prescreening potential employees quick, safe, and extremely easy.....<span>Click more videos</span></p>

<h2 class="abs pricing-h">Pricing</h2>
<table class="abs price">
<tr><td>Interviews:</td><td>5</td><td>10</td><td>25</td><td>50</td></tr>
<tr><td>Price-Per Interview:</td><td style="text-align:left;padding-left:6px">Free<br>(first time user)</td><td>$15 Each</td><td>$10 Each</td><td>$5 Each</td></tr>
<tr><td>Total:</td><td>FREE</td><td>$150.00</td><td>$250.00</td><td>$500.00</td></tr>
<tr><td></td><td></td><td><span class="btn try">TRY IT FREE</span></td><td></td><td></td></tr>
</table>

<div class="abs benefits">
<div class="benefits-h">Benefits</div>
<div class="benefit"><i></i>EASY TO USE &amp; COMPLETELY SELF-DIRECTED</div>
<div class="benefit"><i></i>REDUCE TIME AND COST SPENT INTERVIEWING</div>
<div class="benefit"><i></i>INTERVIEW CANDIDATES FROM WHERE WORLD</div>
<div class="benefit"><i></i>CUSTOMIZE INTERVIEW QUESTIONS IDENTITY</div>
<div class="benefit"><i></i>CUSTOM SECURITY</div>
<div class="benefit"><i></i>IMPROVE TALENT ACQUISITION</div>
<div class="benefit" style="border-bottom:0"><i></i>INVITE ANYONE TO REVIEW CANDIDATES</div>
</div>

<section class="abs admin"></section>
<div class="abs phone" role="img" aria-label="Hand holding a phone showing the candidate list in the admin portal"></div>
<h2 class="abs admin-h">Talksift admin portal</h2>
<p class="abs admin-p">TalkSift is a fully automated video interviewing solution aimed at assisting employers to more efficiently and effectively pre-screen interview candidates before conducting an in-person interview. This unique and fully customizable solution allows employ-ers to view, manage rate, and share candidate video's to expedite the hiring process and reduce the number of costly in-person interviews. TalkSift permits employers of any size to personalize the web solution...</p>
<div class="abs btn read">Read More</div>

<footer class="abs footer"></footer>
<div class="abs social"><i></i><i></i><i></i><i></i></div>
<div class="abs copy">Copyright2014 Talksift.All Right Reseved.</div>
</body>
</html>
```